Lumavento business card

We need a modern business card - With our 4 colors - See web: www.lumavento.dk

I have attached logo and som old business Cards we have - Lets Make the new ones shine...:-) -

Industry/Entity Type

Business

Requirements
Must have
• the logo with lumavento only,

```html
<!DOCTYPE html>
<html lang="da">
<head>
<meta charset="utf-8">
<title>Lumavento – visitkort</title>
<link rel="stylesheet" href="https://fonts.googleapis.com/css2?family=Open+Sans:wght@400;600;700&display=swap">
<style>
  :root {
    --backdrop: #3b3b3b;
    --paper: #ffffff;
    --ink: #2b2b2b;
    --lime: #8dc65a;
    --plum: #6b2a75;
    --berry: #cc3a8c;
    --tangerine: #e5893f;
    --shadow-band: #0d0d0d;
  }
  * { box-sizing: border-box; margin: 0; padding: 0; }
  html, body {
    width: 1105px; height: 1200px; overflow: hidden;
    background: var(--backdrop);
    font-family: "Open Sans", Arial, sans-serif;
  }
  .card {
    position: absolute; left: 192px;
    width: 720px; height: 412px;
    overflow: hidden;
    box-shadow: 0 6px 14px rgba(0,0,0,.45);
  }
  .card--front { top: 145px; }
  .card--back  { top: 602px; }
  .card__art { position: absolute; inset: 0; width: 720px; height: 412px; }

  .holder { position: absolute; left: 36px; top: 32px; }
  .holder__name { color: var(--lime); font-size: 26px; font-weight: 700; line-height: 1.1; }
  .holder__title { color: var(--ink); font-size: 18px; font-weight: 400; margin-top: 2px; }

  .brand { position: absolute; text-align: center; }
  .brand__name {
    display: inline-flex; align-items: center; gap: 9px;
    font-size: 26px; font-weight: 600; line-height: 1;
  }
  .brand__dot { width: 14px; height: 14px; border-radius: 50%; }
  .brand__tagline { font-size: 16px; margin-top: 14px; }

  .card--front .brand { left: 136px; width: 270px; top: 190px; }
  .card--front .brand__name { color: var(--ink); }
  .card--front .brand__dot { background: var(--lime); }
  .card--front .brand__tagline { color: var(--ink); }

  .card--back .brand { left: 540px; width: 180px; top: 298px; }
  .card--back .brand__name { color: var(--paper); font-size: 24px; }
  .card--back .brand__dot { background: var(--paper); width: 12px; height: 12px; }
  .card--back .brand__tagline { color: var(--paper); font-size: 15px; }

  .contact {
    position: absolute; right: 32px; top: 252px; list-style: none;
    text-align: right; color: var(--paper); font-size: 17px; line-height: 28px;
  }
  .contact li { display: flex; justify-content: flex-end; align-items: center; gap: 8px; }
  .contact svg { width: 16px; height: 16px; fill: var(--paper); }
  .contact .contact__address { margin-right: -24px; }
</style>
</head>
<body>

<section class="card card--front" aria-label="Visitkort forside">
  <svg class="card__art" viewBox="0 0 720 412" aria-hidden="true">
    <rect x="0" y="0" width="163" height="412" fill="var(--lime)"/>
    <rect x="163" y="0" width="182" height="412" fill="var(--plum)"/>
    <rect x="345" y="0" width="187" height="412" fill="var(--berry)"/>
    <rect x="532" y="0" width="188" height="412" fill="var(--tangerine)"/>
    <path d="M706 0 H716 C 652 200, 420 350, 0 354 L0 343 C 420 330, 640 190, 706 0 Z" fill="var(--shadow-band)"/>
    <path d="M0 0 H706 C 640 190, 420 330, 0 343 Z" fill="var(--paper)"/>
  </svg>

  <div class="holder">
    <p class="holder__name">Maren Holmgaard</p>
    <p class="holder__title">Salgsdirektør</p>
  </div>

  <div class="brand">
    <p class="brand__name"><span class="brand__dot"></span>Lumavento</p>
    <p class="brand__tagline">ung kommunikation</p>
  </div>

  <ul class="contact">
    <li>+45 30 12 34 56
      <svg viewBox="0 0 24 24"><path d="M6.6 10.8a15 15 0 0 0 6.6 6.6l2.2-2.2a1 1 0 0 1 1-.25 11.4 11.4 0 0 0 3.6.57 1 1 0 0 1 1 1V20a1 1 0 0 1-1 1A17 17 0 0 1 3 4a1 1 0 0 1 1-1h3.5a1 1 0 0 1 1 1c0 1.25.2 2.45.57 3.57a1 1 0 0 1-.25 1z"/></svg></li>
    <li>+45 60 70 80 90
      <svg viewBox="0 0 24 24"><path d="M6.6 10.8a15 15 0 0 0 6.6 6.6l2.2-2.2a1 1 0 0 1 1-.25 11.4 11.4 0 0 0 3.6.57 1 1 0 0 1 1 1V20a1 1 0 0 1-1 1A17 17 0 0 1 3 4a1 1 0 0 1 1-1h3.5a1 1 0 0 1 1 1c0 1.25.2 2.45.57 3.57a1 1 0 0 1-.25 1z"/></svg></li>
    <li>mh@lumavento.dk
      <svg viewBox="0 0 24 24"><path d="M2 5h20v14H2z M2 5l10 8 10-8" stroke="var(--tangerine)" stroke-width="1.2"/></svg></li>
    <li>www.lumavento.dk
      <svg viewBox="0 0 24 24"><circle cx="12" cy="12" r="10"/><path d="M2 12h20M12 2c3 3 3 17 0 20M12 2c-3 3-3 17 0 20" stroke="var(--tangerine)" stroke-width="1.3" fill="none"/></svg></li>
    <li class="contact__address">Solsikkevej 14, 2000 Frederiksberg</li>
  </ul>
</section>

<section class="card card--back" aria-label="Visitkort bagside">
  <svg class="card__art" viewBox="0 0 720 412" aria-hidden="true">
    <rect x="0" y="0" width="177" height="412" fill="var(--lime)"/>
    <rect x="177" y="0" width="178" height="412" fill="var(--plum)"/>
    <rect x="355" y="0" width="184" height="412" fill="var(--berry)"/>
    <rect x="539" y="0" width="181" height="412" fill="var(--tangerine)"/>
    <rect x="354" y="0" width="2" height="412" fill="var(--paper)"/>
    <rect x="538" y="0" width="2" height="412" fill="var(--paper)"/>
  </svg>

  <div class="brand">
    <p class="brand__name"><span class="brand__dot"></span>Lumavento</p>
    <p class="brand__tagline">ung kommunikation</p>
  </div>
</section>

</body>
</html>
```